Blow Dry Bar Business Cards

These cards must be eye catching and modern.
You must be willing to work fast and make changes.

Winner will be offered other projects

Files 1 THIS IS THE STYLE CARDS I AM INTRESTED IN!!!
Please be creative, I am paying for my own eye catching design. I need files to be nexa press ready.

COLORS THAT ARE PAINTED INSIDE MY SHOP:
- - - http://www.quorvelpaint.example/en/explore-colors/painter/color-selector.html?colors=4007-3C

- - - http://www.brandivex.example/color/paint-colors/hidden-corridor-d58-2

I want the business cards sleek and modern if you use the logo please correct imperfections. I added the part that says Blow Dry Bar (see website).
Do not be afraid to separate the blow dryer from the name to make the cards look like the file with the pink elephant.

SHOULD INCLUDE
*Blow Dryer (we are a blow dry bar not a salon we do not cut or color so do not include sheers of any kind)
*BUSINESS NAME: Simply Swept Upward - Blow Dry Bar (PLEASE SEE MY WEBSITE)
* Website: SIMPLYSWEPTUPWARD.EXAMPLE
*Phone number (555) 014-2763
Updates

Nexa press said it can be submitted in JPG

http://www.brandivex.example/color/paint-colors/hidden-corridor-d58-2 http://www.quorvelpaint.example/en/explore-colors/painter/color-selector.html?colors=4007-3C ^^^^ These links will take you to the color paint that is painted inside my shop.

Target Market(s)

AGES 18 - 55 WOMEN
HIGH END MARKET

Industry/Entity Type

Salon

Requirements
Must have
• SEE COLOR EXAMPLE FILE
BLOW DRYER
UNIQUE
I LIKE THE CARD WITH THE PINK ELEPHANT THE BEST
Nice to have
• BE AS CREATIVE AND MODERN AS POSSIBLE DO NOT COPY ANY OF THE CARDS BELOW.
Should not have
• SCISSORS
PINK

```html
<!DOCTYPE html>
<html lang="en">
<head>
<meta charset="utf-8">
<title>Swept Upward – Business Cards</title>
<link href="https://fonts.googleapis.com/css2?family=Arvo&family=Lato:wght@400;700&display=swap" rel="stylesheet">
<style>
  :root {
    --backdrop: #1d1d1f;
    --card: #ffffff;
    --teal: #5fc3cb;
    --brown: #5b3b3d;
    --photo-sky: #f1e6ec;
    --photo-grass: #a8a37a;
    --photo-warm: #d9b8a4;
  }
  * { margin: 0; padding: 0; box-sizing: border-box; }
  html, body { width: 1200px; height: 900px; overflow: hidden; }
  body { background: var(--backdrop); position: relative; font-family: "Lato", sans-serif; }

  .card {
    position: absolute;
    background: var(--card);
    border-radius: 3px;
    overflow: hidden;
    box-shadow: 0 10px 30px rgba(0,0,0,0.5);
  }

  /* Front */
  .card-front { left: 60px; top: 50px; width: 660px; height: 378px; }
  .front-photo {
    position: absolute; right: 0; top: 0; width: 62%; height: 100%;
    background:
      linear-gradient(90deg, #fff 0%, rgba(255,255,255,0) 28%),
      linear-gradient(180deg, var(--photo-sky) 0%, var(--photo-warm) 45%, var(--photo-grass) 100%);
  }
  .front-brand {
    position: absolute; left: 52px; top: 160px;
    display: flex; align-items: center; gap: 12px;
  }
  .brand-dot { width: 22px; height: 22px; border-radius: 50%; background: var(--teal); flex: none; }
  .brand-name { font-family: "Arvo", serif; font-size: 34px; color: var(--teal); font-weight: 400; white-space: nowrap; }

  /* Back */
  .card-back { left: 440px; top: 470px; width: 700px; height: 390px; }
  .back-art {
    position: absolute; left: 0; top: 0; width: 190px; height: 100%;
    background: linear-gradient(90deg, var(--teal) 0%, var(--teal) 70%, rgba(95,195,203,0.85) 100%);
  }
  .back-brand {
    position: absolute; right: 40px; top: 88px;
    display: flex; flex-direction: column; align-items: flex-end;
  }
  .back-brand .brand-row { display: flex; align-items: center; gap: 14px; }
  .back-brand .brand-name { font-size: 46px; }
  .back-brand .brand-dot { width: 30px; height: 30px; }
  .tagline { font-weight: 700; font-size: 26px; color: var(--brown); margin-top: 4px; margin-right: 44px; }
  .service { font-size: 20px; color: var(--brown); margin-top: 2px; margin-right: 44px; }
  .contact {
    position: absolute; right: 36px; bottom: 34px;
    color: var(--brown); font-size: 21px; letter-spacing: 1.5px;
    display: flex; flex-direction: column; align-items: flex-end; gap: 10px;
  }
  .contact-line { display: flex; align-items: center; gap: 10px; white-space: nowrap; }
  .contact-line svg { width: 20px; height: 20px; flex: none; }
</style>
</head>
<body>
  <section class="card card-front">
    <div class="front-photo" role="img" aria-label="Photo of four young women in casual western wear and boots standing on grass"></div>
    <div class="front-brand">
      <span class="brand-dot"></span>
      <span class="brand-name">Swept Upward</span>
    </div>
  </section>

  <section class="card card-back">
    <div class="back-art" role="img" aria-label="Teal illustration of flowing blown hair"></div>
    <div class="back-brand">
      <div class="brand-row">
        <span class="brand-name">Swept Upward</span>
        <span class="brand-dot"></span>
      </div>
      <div class="tagline">Simply Swept Upward</div>
      <div class="service">Blow Dry Bar</div>
    </div>
    <div class="contact">
      <div class="contact-line">
        <span>(555) 014-2763</span>
        <svg viewBox="0 0 20 20" aria-hidden="true"><path d="M4 2 L7 2 L8.5 6 L6.5 7.5 C7.5 10 10 12.5 12.5 13.5 L14 11.5 L18 13 L18 16 C18 17 17 18 16 18 C8.5 17.5 2.5 11.5 2 4 C2 3 3 2 4 2 Z" fill="var(--teal)"/></svg>
      </div>
      <div class="contact-line">
        <span>WWW.SIMPLYSWEPTUPWARD.EXAMPLE</span>
        <svg viewBox="0 0 20 20" aria-hidden="true"><g fill="none" stroke="var(--teal)" stroke-width="1.6"><circle cx="10" cy="10" r="8"/><ellipse cx="10" cy="10" rx="3.5" ry="8"/><line x1="2" y1="10" x2="18" y2="10"/></g></svg>
      </div>
    </div>
  </section>
</body>
</html>
```